Hong Kong based International Remittance and ForEx company requires website design

We need a website designed for a new European - Hong Kong based ForEx & fund remittence entity.

The company specialises in larger corporate & high net worth private client trades, therefore the design must aesthetically reflect this (sophisticated). As a theme colour, financial entities tend to use either blue or red; if blue, our preference is a darker blue. Visually, our preference is less copy, more imagery.

Number of pages would be limited; landing (home), about us, client registration (x1 Corporate form, x1 Private Client form), Contact Us.

Have uploaded the existing logo - please note this is to be redesigned, although the colour scheme will remain the same. Please also note that copy will follow - please use Lorem Ipsum.

Target Market(s)

Medium to large Corporations. High net worth individuals.

Industry/Entity Type

Financial Service

Coding

Coded - Design and coding required

Number of Pages Required

4 page

Font styles to use
Serif

Requirements
Nice to have
• ForEx ticker,

```html
<!DOCTYPE html>
<html lang="en">
<head>
<meta charset="utf-8">
<title>Aldermoor Incorporation Limited</title>
<link href="https://fonts.googleapis.com/css2?family=Open+Sans:wght@400;600&family=Libre+Baskerville&display=swap" rel="stylesheet">
<style>
:root{
  --navy:#1b3a63;
  --navy-band:rgba(16,50,92,.93);
  --red:#c4161c;
  --ink:#222;
  --line:#cfcfcf;
  --dark-panel:#2b2b2b;
  --menu:#222;
  --link-blue:#1f6db5;
  --white:#fff;
}
*{box-sizing:border-box;margin:0;padding:0}
html,body{width:884px;height:1200px;overflow:hidden;background:var(--white)}
body{position:relative;font-family:"Open Sans",Arial,sans-serif;color:var(--ink)}
.abs{position:absolute}

.brand{left:72px;top:12px;width:140px}
.brand-mark{position:absolute;left:92px;top:0;width:24px;height:24px;border-radius:50%;background:#b9c8dd}
.brand-name{position:absolute;left:0;top:30px;font-family:"Libre Baskerville",Georgia,serif;font-size:29px;color:#1e1e1e;letter-spacing:-.5px}
.brand-sub{position:absolute;left:0;top:70px;font-family:"Libre Baskerville",Georgia,serif;font-size:7px;letter-spacing:2.3px;color:#333;white-space:nowrap}

.topinfo{top:34px;right:72px;display:flex;gap:20px;font-size:9.5px;color:#444;letter-spacing:.3px}
.topinfo span{display:flex;align-items:center;gap:6px}
.topinfo svg{width:10px;height:10px}

.nav{top:76px;right:72px;display:flex;gap:23px;font-size:8.6px;font-weight:600;color:#222}
.nav .active{color:var(--red)}

.hero{left:73px;top:109px;width:738px;height:362px;
  background:
    radial-gradient(ellipse 120px 60px at 50% 78%, rgba(214,160,130,.85), rgba(214,160,130,0) 70%),
    radial-gradient(ellipse 240px 110px at 12% 85%, rgba(150,170,200,.9), rgba(150,170,200,0) 70%),
    radial-gradient(ellipse 240px 110px at 88% 85%, rgba(120,140,170,.9), rgba(120,140,170,0) 70%),
    radial-gradient(ellipse 330px 120px at 50% 42%, rgba(120,100,85,.85), rgba(120,100,85,0) 75%),
    radial-gradient(ellipse 300px 90px at 50% 22%, rgba(200,200,200,.55), rgba(200,200,200,0) 70%),
    linear-gradient(90deg,#6c6c6c 0%,#303030 18%,#2a2a2a 82%,#5c6470 100%);}
.hero-band{left:73px;top:407px;width:738px;height:64px;background:var(--navy-band);color:var(--white);font-size:12px;font-weight:600;line-height:19px;padding:14px 0 0 46px}
.register{left:648px;top:424px;width:114px;height:30px;background:var(--red);color:var(--white);font-size:11.5px;font-weight:600;border-radius:2px;display:flex;align-items:center;justify-content:center}
.slide-arrow{width:30px;height:30px;border-radius:50%;background:rgba(255,255,255,.2);top:276px}
.slide-arrow svg{width:30px;height:30px}

.submenu{left:431px;top:109px;width:136px;height:118px;background:var(--menu);border-top:3px solid var(--red);padding-top:18px;font-size:8.8px;color:#f2f2f2}
.submenu li{list-style:none;height:21.6px;padding-left:13px;display:flex;gap:9px}
.submenu li::before{content:"›";color:#4a9be0}

.ticker{left:73px;top:485px;width:738px;height:47px;border:1px solid var(--line);display:flex;align-items:center;padding-left:21px}
.ticker-label{font-size:15px;color:#444;letter-spacing:.3px;width:226px}
.pair{display:flex;align-items:center;width:174px}
.pair b{font-size:11px;color:var(--link-blue);width:62px}
.flag{width:17px;height:11px;margin-right:3px}

.welcome{left:0;width:884px;top:568px;text-align:center;font-size:19.5px;font-weight:600;letter-spacing:.3px}
.intro{left:74px;width:736px;top:604px;text-align:center;font-size:8.6px;line-height:14px;color:#444}
.expertise-title{left:0;width:884px;top:669px;text-align:center;font-size:14px;font-weight:400;color:#333}

.service{top:706px;width:172px}
.service-photo{width:172px;height:132px;box-shadow:0 6px 6px -4px rgba(0,0,0,.35)}
.service-name{position:absolute;top:150px;left:-30px;width:232px;text-align:center;font-size:13.5px;color:#222}

.converter{left:73px;top:952px;width:359px;height:118px;background:var(--dark-panel);color:var(--white);padding:14px 0 0 17px}
.panel-title{font-size:15.5px}
.conv-row{display:flex;margin-top:17px;gap:4px}
.field{height:21px;background:var(--white);color:#444;font-size:8.6px;display:flex;align-items:center;padding-left:9px;justify-content:space-between;padding-right:7px}
.conv-result{font-size:7.8px;margin-top:10px}

.clients{left:451px;top:952px;width:360px;height:118px;border:1px solid #bbb;padding:14px 0 0 16px}
.clients .panel-title{color:#333}
.client-row{display:flex;align-items:center;margin-top:28px;gap:22px;font-size:10px;color:#333}
.client-row .dot{width:14px;height:14px;border-radius:50%;display:inline-block;vertical-align:middle;margin-right:4px}
.badge{width:28px;height:28px;border-radius:50%;background:#c9a53a}

.footer{left:0;top:1142px;width:884px;height:58px;background:var(--navy);color:#dde;display:flex;align-items:center;padding:0 72px;justify-content:space-between;font-size:10.5px}
.social{display:flex;gap:14px;font-size:9.5px;font-weight:600}
</style>
</head>
<body>

<div class="abs brand">
  <div class="brand-mark"></div>
  <div class="brand-name">Aldermoor</div>
  <div class="brand-sub">INCORPORATION LIMITED</div>
</div>

<div class="abs topinfo">
  <span><svg viewBox="0 0 10 10"><circle cx="5" cy="5" r="4.5" fill="#2a7cc0"/></svg>Language: English</span>
  <span><svg viewBox="0 0 10 10"><path d="M2 1 L4 1 L4.5 3 L3.3 4 Q4.5 6 6 6.8 L7 5.5 L9 6 L9 8 Q5 9.5 1 3 Z" fill="#2a7cc0"/></svg>(555) 01234567</span>
  <span><svg viewBox="0 0 10 10"><circle cx="5" cy="5" r="4" fill="none" stroke="#2a7cc0" stroke-width="1.2"/><path d="M5 2.5V5H7" stroke="#2a7cc0" fill="none"/></svg>Mon - Sat: 9:00 - 18:00</span>
</div>

<nav class="abs nav">
  <span>HOME</span><span class="active">ABOUT US</span><span>INTERNATIONAL PAYMENTS</span><span>CLIENT APPLICATION</span><span>CONTACT US</span>
</nav>

<div class="abs hero" role="img" aria-label="Business team in suits standing behind a close-up handshake"></div>
<div class="abs slide-arrow" style="left:97px"><svg viewBox="0 0 30 30"><path d="M17 9l-6 6 6 6" stroke="#ddd" stroke-width="2.5" fill="none"/></svg></div>
<div class="abs slide-arrow" style="left:760px"><svg viewBox="0 0 30 30"><path d="M13 9l6 6-6 6" stroke="#ddd" stroke-width="2.5" fill="none"/></svg></div>

<ul class="abs submenu">
  <li>Affiliates</li><li>Our</li><li>Ethos</li><li>FAQ's</li>
</ul>

<div class="abs hero-band">We are a new ForEx &amp; fund remittance entity based in European - Hong Kong.<br>We Excel in larger corporate &amp; high net worth private client trades.</div>
<div class="abs register">Register Now</div>

<div class="abs ticker">
  <div class="ticker-label">FOREX TICKER:</div>
  <div class="pair"><b>123</b>
    <svg class="flag" viewBox="0 0 17 11"><rect width="17" height="11" fill="#b22"/><rect y="2" width="17" height="1.5" fill="#fff"/><rect y="5" width="17" height="1.5" fill="#fff"/><rect y="8" width="17" height="1.5" fill="#fff"/><rect width="8" height="6" fill="#2a3f8a"/></svg>
    <svg class="flag" viewBox="0 0 17 11"><rect width="17" height="11" fill="#d22"/><rect x="7" y="2" width="3" height="7" fill="#fff"/><rect x="5" y="4" width="7" height="3" fill="#fff"/></svg>
  </div>
  <div class="pair"><b>123</b>
    <svg class="flag" viewBox="0 0 17 11"><rect width="17" height="11" fill="#1c2f7a"/><rect width="8" height="5" fill="#c33"/><circle cx="13" cy="7" r="1" fill="#fff"/></svg>
    <svg class="flag" viewBox="0 0 17 11"><rect width="17" height="11" fill="#b22"/><rect y="2" width="17" height="1.5" fill="#fff"/><rect y="5" width="17" height="1.5" fill="#fff"/><rect y="8" width="17" height="1.5" fill="#fff"/><rect width="8" height="6" fill="#2a3f8a"/></svg>
  </div>
  <div class="pair"><b>123</b>
    <svg class="flag" viewBox="0 0 17 11"><rect width="17" height="11" fill="#1f3a99"/><circle cx="8.5" cy="5.5" r="3" fill="none" stroke="#fc0" stroke-dasharray="1 1.2"/></svg>
    <svg class="flag" viewBox="0 0 17 11"><rect width="17" height="11" fill="#1c2f7a"/><path d="M0 0L17 11M17 0L0 11" stroke="#fff" stroke-width="2"/><rect x="7" width="3" height="11" fill="#fff"/><rect y="4" width="17" height="3" fill="#fff"/><rect x="7.7" width="1.6" height="11" fill="#c22"/><rect y="4.7" width="17" height="1.6" fill="#c22"/></svg>
  </div>
</div>

<h1 class="abs welcome">WELCOME TO OUR SITE</h1>
<p class="abs intro">Aldermoor Incorporation Limited is a regulated Money Service Operator Number (18-04-02291), licensed authorised by the Hong Kong Customs and Excise. We provide the international settlement and reconciliation of funds for and on behalf of our clients which include both corporates and individuals.  As well as acting as a remittance entity we also provide foreign exchange services and work closely with our clients to source the most cost effective rates.  Drawing on our experience in the provision of international financial services we ensure that our clients receive the most cost effective and efficient money remittance and foreign exchange services.</p>
<h2 class="abs expertise-title">Expertise</h2>

<div class="abs service" style="left:142px">
  <div class="service-photo" role="img" aria-label="Businessman touching a glowing world map" style="background:linear-gradient(135deg,#0e2a55,#2f7bc4 55%,#0b1f3d)"></div>
  <div class="service-name">International Money Transfer</div>
</div>
<div class="abs service" style="left:357px">
  <div class="service-photo" role="img" aria-label="Assorted banknotes fanned together" style="background:linear-gradient(135deg,#c79b4a,#e06a55 45%,#b9bf9a 80%)"></div>
  <div class="service-name">Foreign Exchange</div>
</div>
<div class="abs service" style="left:571px">
  <div class="service-photo" role="img" aria-label="Adviser reviewing documents with an older couple" style="background:linear-gradient(135deg,#8fa0b6,#d9d4cc 50%,#7d8fa5)"></div>
  <div class="service-name">Paying &amp; Receiving Agency</div>
</div>

<div class="abs converter">
  <div class="panel-title">Currency Converter</div>
  <div class="conv-row">
    <div class="field" style="width:51px">200</div>
    <div class="field" style="width:94px">British Pound<svg width="8" height="5" viewBox="0 0 8 5"><path d="M1 1l3 3 3-3" stroke="#444" fill="none"/></svg></div>
    <div style="width:24px"></div>
    <div class="field" style="width:51px">200</div>
    <div class="field" style="width:94px">British Pound<svg width="8" height="5" viewBox="0 0 8 5"><path d="M1 1l3 3 3-3" stroke="#444" fill="none"/></svg></div>
  </div>
  <div class="conv-result">100.00 British Pound Sterling is 1,077.500</div>
</div>

<div class="abs clients">
  <div class="panel-title">Our Clients</div>
  <div class="client-row">
    <span><span class="dot" style="background:#e28b1c"></span>Northwind Systems</span>
    <span>Larkspur</span>
    <span>Brightfield Tech</span>
    <span class="badge"></span>
  </div>
</div>

<footer class="abs footer">
  <div class="social"><span>Flock</span><span>Lens</span><span>Folio</span><span>Orbit</span></div>
  <div>© yoursite - 2016 All Rights Reserved</div>
</footer>

</body>
</html>
```